Company Flyer for Electric boating company

I am looking for a company flyer which we can hand over to boat owners in the Netherlands (Amsterdam area). Our core business is to rebuild every boat (from 4 to 10 meters) into an electrically propelled boat. We are taking out diesels and replace them with a high quality electrical motor, inboard varying from 30 till 80 pk (hp). And outboard from 1pk (hp) till 200pk. We are the best, not the cheapest, not the most expensive. We only work with the best materials. The flyer has to be sort of in line with our website and branding.

Major advantages of electric boating are:
- completely silent
- no fumes, smells or smoke
- cheap to operate
- environmentally friendly
- obliged in more and more areas
- no maintenance
- more enjoyable

The flyer should be A5 format. Since all the text has to be in Dutch I expect only the graphical design and layout for advantages, process, pricing and contact details etc.

Target Market(s)

Boat owners in the Netherlands

Font styles to use
Sans Serif

Colors
9bcb3c
add136
cadf82
0555a3
3176b5
85acd3
e0ebf3

Requirements
Must have
• Clean design, in line with website: www.volthaven.nl
Nice to have
• icons for advantages, boating etc

2 sides
Should not have
• Steering wheel...

```html
<!DOCTYPE html>
<html lang="en">
<head>
<meta charset="utf-8">
<title>Volthaven Flyer</title>
<link rel="stylesheet" href="https://fonts.googleapis.com/css2?family=Montserrat:wght@300;400;500;600;700;800&display=swap">
<style>
  :root {
    --green: #84bf04;
    --navy: #353a4c;
    --navy-deep: #1e2a36;
    --white: #ffffff;
    --paper: #f4f5f6;
    --text: #2f3445;
    --stage: #5a5a5a;
  }
  * { margin: 0; padding: 0; box-sizing: border-box; }
  html, body { width: 900px; height: 1200px; overflow: hidden; background: var(--stage); }
  body { font-family: "Montserrat", sans-serif; }
  .flyer {
    position: absolute; left: 27px; top: 0; width: 846px; height: 1200px;
    background: var(--white); overflow: hidden;
  }
  .header { position: absolute; inset: 0 0 auto 0; height: 175px; }
  .header-shapes { position: absolute; inset: 0; }
  .brand { position: absolute; left: 57px; top: 58px; display: flex; align-items: center; gap: 18px; }
  .brand-dot { width: 64px; height: 64px; border-radius: 50%; background: var(--navy); }
  .brand-name { font-weight: 800; font-size: 40px; color: var(--green); letter-spacing: 0.5px; }
  .contact { position: absolute; right: 48px; top: 58px; color: var(--white); font-size: 21px; }
  .contact-line { display: flex; align-items: center; gap: 8px; height: 41px; }
  .contact-line.web { font-weight: 500; }
  .contact-line.phone { font-weight: 700; }
  .hero {
    position: absolute; left: 0; top: 175px; width: 846px; height: 437px;
    background: radial-gradient(ellipse at 50% 35%, #7d8c95 0%, #3d4c58 35%, #16212c 80%);
  }
  .headline { position: absolute; left: 0; width: 100%; top: 148px; text-align: center; color: var(--white); }
  .headline-line { font-size: 51px; line-height: 66px; text-transform: uppercase; white-space: nowrap; }
  .bold { font-weight: 800; }
  .light { font-weight: 300; }
  .accent { color: var(--green); }
  .tagline-bar {
    position: absolute; left: 56px; top: 359px; width: 734px; height: 38px;
    background: var(--green); color: var(--white); font-weight: 700; font-size: 18px;
    display: flex; align-items: center; justify-content: center; white-space: nowrap;
  }
  .advantages-title {
    position: absolute; left: 0; top: 612px; width: 846px; height: 59px;
    background: var(--navy); color: var(--white); font-size: 32px;
    display: flex; align-items: center; justify-content: center; gap: 10px; white-space: nowrap;
  }
  .advantages-title .light { font-weight: 300; }
  .advantages-title .accent { font-weight: 800; }
  .advantages { position: absolute; left: 0; top: 671px; width: 846px; height: 412px; background: var(--paper); }
  .advantage { position: absolute; display: flex; align-items: center; }
  .advantage-icon { width: 52px; height: 52px; }
  .advantage-rule { width: 2px; height: 54px; background: var(--green); margin: 0 12px 0 10px; }
  .advantage-text { font-size: 20px; font-weight: 500; color: var(--text); line-height: 25px; }
  .motor-render {
    position: absolute; left: 573px; top: 16px; width: 208px; height: 303px;
    background: radial-gradient(ellipse at 50% 45%, #9a9ea3 0%, #d6d8da 60%, #f4f5f6 100%);
    border-radius: 18px;
  }
  .footer-band { position: absolute; left: 0; top: 1083px; width: 846px; height: 117px; background: var(--navy); }
  .gallery-photo { position: absolute; top: 1006px; width: 177px; height: 134px; }
  .photo-frame { position: absolute; inset: 6px; border: 1px solid rgba(255,255,255,0.8); }
  .footer-info {
    position: absolute; left: 49px; right: 48px; top: 1152px; color: var(--white);
    font-size: 17px; display: flex; align-items: center; gap: 10px; white-space: nowrap;
  }
  .footer-sep { margin: 0 22px; }
</style>
</head>
<body>
<main class="flyer">
  <header class="header">
    <svg class="header-shapes" width="846" height="175" viewBox="0 0 846 175">
      <polygon points="542,66 556,66 486,175 472,175" fill="var(--navy)"/>
      <polygon points="579,0 846,0 846,175 502,175" fill="var(--green)"/>
    </svg>
    <div class="brand">
      <span class="brand-dot"></span>
      <span class="brand-name">VOLTHAVEN</span>
    </div>
    <div class="contact">
      <div class="contact-line web">
        <svg width="17" height="17" viewBox="0 0 20 20" fill="none" stroke="#fff" stroke-width="1.6"><circle cx="10" cy="10" r="8"/><ellipse cx="10" cy="10" rx="3.5" ry="8"/><line x1="2" y1="10" x2="18" y2="10"/></svg>
        www.volthaven.nl
      </div>
      <div class="contact-line phone">
        <svg width="17" height="17" viewBox="0 0 20 20" fill="none" stroke="#fff" stroke-width="1.6"><circle cx="10" cy="10" r="8.5"/><path d="M7 5.5l2 2.5-1 1.2c.6 1.2 1.6 2.2 2.8 2.8l1.2-1 2.5 2-1.2 1.5c-3.5-.3-6.8-3.6-7.1-7.1z"/></svg>
        +31 6 00 482 917
      </div>
    </div>
  </header>

  <section class="hero" role="img" aria-label="Photo from the stern of a boat: two electric outboard motors churning white water">
    <div class="headline">
      <div class="headline-line"><span class="bold">Rebuild</span> <span class="light">your</span> <span class="bold accent">boat</span></div>
      <div class="headline-line"><span class="light">into an</span> <span class="bold accent">electrically</span></div>
      <div class="headline-line bold">propelled boat</div>
    </div>
    <div class="tagline-bar">WE ARE THE BEST, NOT THE CHEAPEST, NOT THE MOST EXPENSIVE.</div>
  </section>

  <h2 class="advantages-title"><span class="light">ADVANTAGES OF</span> <span class="accent">ELECTRIC BOATING ARE:</span></h2>

  <section class="advantages">
    <div class="advantage" style="left:53px; top:33px;">
      <svg class="advantage-icon" viewBox="0 0 52 52" fill="none" stroke="var(--green)" stroke-width="2.2" stroke-linecap="round" stroke-linejoin="round"><path d="M6 20h8l12-9v30l-12-9H6z"/><path d="M32 20c3 3 3 9 0 12M37 15c6 6 6 16 0 22"/><line x1="10" y1="46" x2="40" y2="6"/></svg>
      <span class="advantage-rule"></span>
      <span class="advantage-text">Completely<br>Silent</span>
    </div>
    <div class="advantage" style="left:53px; top:141px;">
      <svg class="advantage-icon" viewBox="0 0 52 52" fill="none" stroke="var(--green)" stroke-width="2.2" stroke-linecap="round" stroke-linejoin="round"><rect x="4" y="8" width="42" height="20" rx="2"/><circle cx="25" cy="18" r="6"/><path d="M8 34h8v6H8zM20 34h8v6h-8zM36 32v14M32 42l4 4 4-4"/></svg>
      <span class="advantage-rule"></span>
      <span class="advantage-text">Cheap<br>To Operate</span>
    </div>
    <div class="advantage" style="left:53px; top:250px;">
      <svg class="advantage-icon" viewBox="0 0 52 52" fill="none" stroke="var(--green)" stroke-width="2.2" stroke-linecap="round" stroke-linejoin="round"><path d="M3 28h46l-6 8H9z"/><path d="M14 28l4-6h16l4 6"/><path d="M2 42c5-3 9 3 14 0s9 3 14 0 9 3 14 0"/></svg>
      <span class="advantage-rule"></span>
      <span class="advantage-text">More<br>Enjoyable</span>
    </div>
    <div class="advantage" style="left:290px; top:36px;">
      <svg class="advantage-icon" viewBox="0 0 52 52" fill="none" stroke="var(--green)" stroke-width="2.2" stroke-linecap="round"><circle cx="26" cy="26" r="22"/><circle cx="26" cy="26" r="14"/><circle cx="26" cy="26" r="6"/><line x1="26" y1="4" x2="26" y2="48"/><line x1="4" y1="26" x2="48" y2="26"/><line x1="26" y1="26" x2="41" y2="11"/></svg>
      <span class="advantage-rule"></span>
      <span class="advantage-text">Obliged In More<br>And More Areas</span>
    </div>
    <div class="advantage" style="left:290px; top:104px;">
      <svg class="advantage-icon" viewBox="0 0 52 52" fill="none" stroke="var(--green)" stroke-width="2.2" stroke-linecap="round" stroke-linejoin="round"><path d="M10 6l8 8-4 4-8-8M16 16l24 24"/><circle cx="42" cy="42" r="5"/><path d="M44 8a8 8 0 0 0-10 10L10 42a3 3 0 0 0 4 4l24-24a8 8 0 0 0 10-10l-5 5-4-4z"/></svg>
      <span class="advantage-rule"></span>
      <span class="advantage-text">No Maintenance</span>
    </div>
    <div class="advantage" style="left:290px; top:170px;">
      <svg class="advantage-icon" viewBox="0 0 52 52" fill="none" stroke="var(--green)" stroke-width="2.2" stroke-linecap="round" stroke-linejoin="round"><path d="M16 26c-4-4 0-10 5-8 1-6 10-6 11 0 5-1 7 5 3 8"/><path d="M6 40l34-6 6 4-6 6H8z"/><line x1="6" y1="50" x2="44" y2="4"/></svg>
      <span class="advantage-rule"></span>
      <span class="advantage-text">No Fumes, Smells<br>Or Smoke</span>
    </div>
    <div class="advantage" style="left:290px; top:250px;">
      <svg class="advantage-icon" viewBox="0 0 52 52" fill="none" stroke="var(--green)" stroke-width="2.2" stroke-linecap="round" stroke-linejoin="round"><path d="M26 6c8 6 8 16 0 22-8-6-8-16 0-22zM26 14v26"/><path d="M4 22l6 14 8 6v6M48 22l-6 14-8 6v6"/></svg>
      <span class="advantage-rule"></span>
      <span class="advantage-text">Environmentally<br>Friendly</span>
    </div>
    <div class="motor-render" role="img" aria-label="Technical wireframe render of an electric inboard motor"></div>
  </section>

  <div class="footer-band"></div>
  <div class="gallery-photo" style="left:49px; background:linear-gradient(#8c959a 0%, #5d6870 45%, #6f7f7c 100%);" role="img" aria-label="Photo of a dark electric sloop moored in a marina"><span class="photo-frame"></span></div>
  <div class="gallery-photo" style="left:239px; background:linear-gradient(#b7c0c6 0%, #7f8a8f 45%, #4f5b60 100%);" role="img" aria-label="Photo of people cruising in an electric sloop past moored yachts"><span class="photo-frame"></span></div>
  <div class="gallery-photo" style="left:429px; background:linear-gradient(#c2c8c9 0%, #4a5258 45%, #7a8480 100%);" role="img" aria-label="Photo of a black electric boat moored at a quay"><span class="photo-frame"></span></div>
  <div class="gallery-photo" style="left:620px; background:linear-gradient(#cfd9e0 0%, #8a949a 50%, #5c6a70 100%);" role="img" aria-label="Photo of an electric sloop on a city canal with apartment blocks behind"><span class="photo-frame"></span></div>

  <footer class="footer-info">
    <svg width="12" height="16" viewBox="0 0 12 16" fill="none" stroke="var(--green)" stroke-width="1.6"><path d="M6 15S1 9 1 6a5 5 0 0 1 10 0c0 3-5 9-5 9z"/><circle cx="6" cy="6" r="1.8"/></svg>
    <span>Havenkade 12B, 1021AB, Amsterdam (Noord), Nederland</span>
    <span class="footer-sep">|</span>
    <svg width="20" height="14" viewBox="0 0 20 14" fill="none" stroke="var(--green)" stroke-width="1.6"><rect x="1" y="1" width="18" height="12"/><path d="M1 1l9 7 9-7"/></svg>
    <span>info@volthaven.nl</span>
  </footer>
</main>
</body>
</html>
```